Brochure for a civil enineering company in A4 format

I need a brochure design for our company TIRO Engineering S.r.l.. We are an engineering consultant company. Our main clients are from the infrastructure industry (geotechnical and underground sectors mainly).
We are looking for a 2 pages (4 faces) fold out design with a glued pocket where we can put individual data sheets.
I need A4 format pages.

Target Market(s)

We are an engineering consultant company. Our main clients are from the infrastructure industry (geotechnical and underground sectors mainly).

Industry/Entity Type

Civil Engineer

Font styles to use
Sans Serif

Requirements
Must have
• Overall: 2 pages in A4 format
Essential style. Bright and modern appearance.
Glued pocket
Logo integrated in a picture on the pocket where I would like to insert a slogan (… tiro engineering … reliable solutions …)
Attached are selected images which the designer can use and edit at their own discretion.
Some advice in the following (anyway designers are free to provide their solutions):
Outer sheets:
Front page with name, logo. It could be nice to have the “m” of the logo integrated in a pictures, also a modified picture (I mean modify one of the attached pictures) so to create a general image and do not tie the cover to a specific job.
Back page: offices address and contact email address. Nice to have one space for a slogan.
Inner sheet: text that I upload in the file “inside-sheets”, possibly with pictures on each sheet. In the right faces insert the glued pocket. On this pages insert the section OUR EXPERIENCE ….with a space for a picture of our team.
Nice to have
• Clean and essential design.
Pictures choosing from the atteched ones. Pictures could be modified in a very light manner to make them a general idea of the work ( I mean geotechnical world) without to be immediately linked to a specific site.
Should not have
• excessive frills

```html
<!DOCTYPE html>
<html lang="it">
<head>
<meta charset="utf-8">
<title>TIRO Engineering – Brochure</title>
<link href="https://fonts.googleapis.com/css2?family=Source+Sans+3:wght@300;400;600&family=Source+Code+Pro:wght@400&display=swap" rel="stylesheet">
<style>
  :root{
    --black:#000;
    --ink:#3a3a3a;
    --mid:#5a5a5a;
    --panel-grey:#d1d2d4;
    --dark-panel:#3a3a3a;
    --logo-light:#8c8c8c;
    --paper:#fff;
    --line:#444;
    --photo-a:#6d6d6d;
    --photo-b:#b9b9b9;
  }
  *{margin:0;padding:0;box-sizing:border-box}
  html,body{width:860px;height:1200px;overflow:hidden;background:var(--paper)}
  body{position:relative;font-family:"Source Sans 3",sans-serif;color:var(--ink)}
  .spread{position:absolute;left:44px;width:756px;border:1px solid var(--line)}
  .spread--outer{top:41px;height:534px}
  .spread--inner{top:594px;height:601px;background:var(--paper)}
  .face{position:absolute;top:0;height:100%}
  .face--back{left:0;width:378px;background:var(--black)}
  .face--cover{left:378px;width:378px;background:var(--panel-grey);border-left:1px solid var(--line)}
  .face--left{left:0;width:378px}
  .face--right{left:378px;width:378px;border-left:1px solid var(--line)}

  .offices{position:absolute;left:182px;top:392px;color:#e6e6e6;font-size:6.2px;line-height:7.8px}
  .offices__title{letter-spacing:1.3px;text-decoration:underline;margin-bottom:6px;font-size:6.4px}
  .offices__city{font-weight:600;color:#fff}
  .offices p{margin-bottom:7px}
  .offices__web{font-weight:600;color:#fff}

  .brand{position:absolute;text-align:center}
  .brand__name{font-weight:600;font-size:56px;line-height:1;letter-spacing:1px}
  .brand__tag{font-family:"Source Code Pro",monospace;font-size:6.4px;letter-spacing:1.6px;margin-top:4px;white-space:nowrap}
  .brand--cover{left:0;width:378px;top:58px;color:var(--ink)}
  .brand--pocket{left:0;width:100%;top:66px;color:var(--logo-light)}

  .photo{position:absolute;background:linear-gradient(160deg,var(--photo-b),var(--photo-a))}
  .photo--cover{left:0;top:204px;width:378px;height:330px;border-radius:180px 180px 0 0}
  .photo--tunnel{left:207px;top:0;width:162px;height:218px}
  .photo--site{left:35px;top:414px;width:343px;height:144px}

  .heading{position:absolute;font-weight:300;font-size:24.5px;line-height:22px;color:var(--mid);letter-spacing:-.2px}
  .text{position:absolute;font-size:5.35px;line-height:8.1px;color:#333;overflow:hidden}
  .text p{margin:0}
  .bullets{list-style:none}
  .bullets li{position:relative;padding-left:8px;margin-bottom:3px}
  .bullets li::before{content:"•";position:absolute;left:0}

  .pocket{position:absolute;left:22px;top:365px;width:355px;height:236px;background:var(--dark-panel);border-radius:42px 0 0 0}
</style>
</head>
<body>

<section class="spread spread--outer">
  <div class="face face--back">
    <div class="offices">
      <div class="offices__title">OUR OFFICES</div>
      <p><span class="offices__city">Milano</span><br>Via Verdi, 14<br>20100 Milano - IT<br>T: +39 02 000111222<br>E: info@tiroengineering.org</p>
      <p><span class="offices__city">Arco TN</span><br>Via S. MARCO, 9<br>32000 Arco TN - IT<br>T: +39 02 000111222<br>E: info@tiroengineering.org</p>
      <p class="offices__web">Web: www.tiroengineering.org</p>
    </div>
  </div>
  <div class="face face--cover">
    <div class="brand brand--cover">
      <div class="brand__name">tiro</div>
      <div class="brand__tag">TIRO ENGINEERING , RELIABLE SOLUTIONS</div>
    </div>
    <div class="photo photo--cover" role="img" aria-label="Black and white photo of a large construction site with scaffolding and excavation"></div>
  </div>
</section>

<section class="spread spread--inner">
  <div class="face face--left">
    <div class="photo photo--tunnel" role="img" aria-label="Black and white photo of a tunnel boring machine shield lifted by a crane into a shaft"></div>
    <h2 class="heading" style="left:35px;top:34px">OUR COMPANY</h2>
    <div class="text" style="left:35px;top:62px;width:160px;height:162px">
      <p>TIRO Engineering S.r.l. offre servizi di consulenza tecnica, contrattuale e strategica ai principali attori nei settori delle scienze geologiche, dell'ingegneria geotecnica e dell'ingegneria idraulica. Lavoriamo per mitigare il rischio e ridurre l'incertezza, con flessibilità nella ricerca della soluzione ottimale contribuendo ad aumentare la redditività del progetto.</p>
      <p>TIRO Engineering S.r.l. è una società indipendente che nasce nel luglio 2020 dall'associazione di un gruppo di professionisti che hanno messo a fattor comune la reciproca esperienza maturata in oltre trent'anni di attività come progettisti e consulenti nel settore delle grandi opere di ingegneria civile lavorando come Direttori Tecnici di Main Engineering Companies and as Freelancers.</p>
      <p>TIRO Engineering S.r.l. vuole unire l'esperienza dei Fondatori e delle figure chiave con l'entusiasmo di chi intraprende una nuova attività, per dare vita ad una nuova realtà che pone come obiettivo principale il design of infrastructures that are safe, sustainable and economic.</p>
      <p>Each of our projects represents a long term commitment, we believe in providing safe, reliable, sustainable and innovative solutions. This is and will be our distinctive characteristic.</p>
    </div>

    <h2 class="heading" style="left:35px;top:236px">OUR SERVICES</h2>
    <div class="text" style="left:35px;top:264px;width:160px;height:140px">
      <p>Progettazione e consulenza specialistica nel campo della geologia, dell'ingegneria geotecnica, delle opere sotterranee e dell'ingegneria idraulica.</p>
      <p>Aiutiamo i nostri clienti a risolvere problemi di natura progettuale, contrattuale e costruttiva che possono nascere nell'intera vita del progetto portando la nostra esperienza all'interno delle loro organizzazioni, migliorando la qualità dei loro servizi di ingegneria, ottimizzando i loro progetti, proponendo nuove idee e soluzioni, rafforzando i loro approcci ……</p>
      <p>TIRO Engineering è in grado di fornire la propria assistenza nell'intero iter procedurale, dalla fase di indagine preliminare e di analisi di fattibilità fino alla progettazione costruttiva e all'assistenza tecnica in fase realizzativa.</p>
      <p>La specializzazione e l'esperienza accumulate nelle discipline della geologia, dell'ingegneria geotecnica e del sottosuolo e dell'idraulica ci permette di massimizzare la nostra efficacia quando sia necessario:</p>
    </div>
    <ul class="text bullets" style="left:202px;top:264px;width:150px;height:140px">
      <li>far fronte a situazioni di emergenza anche su progetti in fase di sviluppo avanzato garantendo l'immediata focalizzazione delle problematiche di progetto e garantendo il risultato finale atteso (in termini di qualità, tempistiche e costi…)</li>
      <li>fornire “second opinion” di elevato valore tecnico ed amministrativo in occasione di problematiche progettuali e costruttive e dispute legali</li>
      <li>analizzare in tempi brevi progetti svolti da terzi individuandone le “criticità”, verificandone la cantierabilità e la validità tecnico economica.</li>
      <li>ottimizzare i progetti redatti da terzi implementandone il contenuto e massimizzando l'efficacia economica degli investimenti.</li>
    </ul>
    <div class="photo photo--site" role="img" aria-label="Black and white photo of an excavator and trucks working in a large earthwork pit"></div>
  </div>

  <div class="face face--right">
    <h2 class="heading" style="left:21px;top:34px">OUR EXPERTISE AND<br>EXPERIENCE</h2>
    <div class="text" style="left:21px;top:84px;width:142px;height:250px">
      <p>La società nasce dall'associazione di un gruppo di professionisti, con indiscusse competenze ed affidabilità, con esperienza maturata in oltre trent'anni di attività come progettisti e consulenti nel settore delle grandi opere di ingegneria civile; geologia, ingegneria geotecnica ed idraulica ed opere sotterranee sono il “core” delle loro competenze ….</p>
      <p>I soci fondatori sono:</p>
      <p>Marco. Già Direttore Tecnico e Socio di RVTA Srl, nel periodo di sua permanenza fino al dicembre 2018, ha per essa firmato tutti i progetti nel campo delle opere sotterranee e la maggior parte di quelli di ingegneria geotecnica. Da gennaio 2019 è Direttore Tecnico di GTSN. Può vantare più di 150 gallerie naturali, e numerosi progetti ed assistenze tecniche nel campo delle strutture geotecniche, delle sistemazioni idrogeologiche e dei versanti e delle opere di protezione ambientale. Negli ultimi dieci anni è stato responsabile di attività di assistenza tecnica, per imprese di costruzione, di opere il cui valore supera i 440 Mio EUR e di servizi di progettazione definitiva e/o esecutiva per opere il cui valore supera i 1.400 Mio EUR.</p>
      <p>Luca 30 anni di esperienza professionale. Coinvolto in più di 150 gallerie naturali con lunghezza complessiva superiore a 360 km. Numerosi progetti ed attività di assistenza tecnica nel campo delle strutture e dei versanti. Negli ultimi dieci anni responsabile di attività di assistenza tecnica in corso d'opera, per imprese di costruzione, di opere il cui</p>
    </div>
    <div class="text" style="left:172px;top:84px;width:142px;height:250px">
      <p>valore supera i 440 Mio EUR e di servizi di progettazione definitiva o esecutiva per opere il cui valore supera i 1.400 Mio EUR. Ha svolto attività di verifica ai fini della validazione, in Italia ed all'estero, di numerosi progetti il cui valore complessivo supera i 3.400 Mio EUR.</p>
      <p>Giulia 30 anni di esperienza professionale. Coinvolta in più di 150 gallerie naturali con lunghezza complessiva superiore a 360 km. Numerosi progetti ed attività di assistenza tecnica nel campo delle strutture, delle sistemazioni idrogeologiche e dei versanti e delle opere di protezione ambientale. Negli ultimi dieci anni responsabile di attività di assistenza tecnica in corso d'opera, per imprese di costruzione, di opere il cui valore supera i 440 Mio EUR e di servizi di progettazione per opere il cui valore supera i 1.400 Mio EUR. Ha svolto attività di verifica ai fini della validazione di numerosi progetti.</p>
      <p>Elena 30 anni di esperienza professionale. Coinvolta in più di 150 gallerie naturali con lunghezza complessiva superiore a 360 km. Numerosi progetti ed attività di assistenza tecnica nel campo delle strutture, delle sistemazioni idrogeologiche e dei versanti e delle opere di protezione ambientale. Negli ultimi dieci anni responsabile di attività di assistenza tecnica in corso d'opera, di opere il cui valore supera i 440 Mio EUR. Ha svolto attività di verifica ai fini della validazione, in Italia ed all'estero, di numerosi progetti il cui valore complessivo supera i 3.400 Mio EUR.</p>
    </div>
    <div class="pocket">
      <div class="brand brand--pocket">
        <div class="brand__name">tiro</div>
        <div class="brand__tag">TIRO ENGINEERING , RELIABLE SOLUTIONS</div>
      </div>
    </div>
  </div>
</section>

</body>
</html>
```